Executive Coaching and Spiritual Development Company needs a business card design.

We need a business card design for our company. We already have a logo that was created through Brightloom that we will submit and would like to see this work on black, blue and white backgrounds. Our personal information should be included as well. The design should communicate trust, spirituality, support and partnership.

Industry/Entity Type

Business

Colors
0255a3
33a6d7
ffffff
000000
474747

Requirements
Nice to have
• The colors offered here are just ideas--we are open to other suggestions, too.

```html
<!DOCTYPE html>
<html lang="en">
<head>
<meta charset="utf-8">
<title>Lumenway Business Card</title>
<link href="https://fonts.googleapis.com/css2?family=Lato:wght@300;400;700;900&family=Josefin+Sans:wght@400;600&display=swap" rel="stylesheet">
<style>
  :root {
    --brand-blue: #0255a3;
    --brand-sky: #33a6d7;
    --ink: #1a2433;
    --text-dark: #222222;
    --grey: #474747;
    --card: #ffffff;
    --stage: #e9ebee;
    --faint: #d9dadd;
  }
  * { margin: 0; padding: 0; box-sizing: border-box; }
  html, body { width: 1200px; height: 764px; overflow: hidden; }
  body { background: var(--stage); position: relative; font-family: "Lato", sans-serif; }

  .card {
    position: absolute;
    width: 560px;
    height: 320px;
    background: var(--card);
    overflow: hidden;
    box-shadow: 0 6px 18px rgba(0,0,0,0.18);
  }
  .card--back { left: 60px; top: 60px; }
  .card--front { left: 580px; top: 384px; }

  .card__bands { position: absolute; inset: 0; width: 560px; height: 320px; }

  .brand {
    position: absolute;
    display: flex;
    align-items: center;
    gap: 16px;
  }
  .brand__mark {
    border-radius: 50%;
    background: var(--brand-blue);
    flex: none;
  }
  .brand__name {
    font-family: "Lato", sans-serif;
    font-weight: 700;
    color: var(--ink);
    line-height: 1;
  }
  .card--back .brand { left: 140px; top: 120px; }
  .card--back .brand__mark { width: 80px; height: 80px; }
  .card--back .brand__name { font-size: 58px; }

  .card--front .brand { left: 40px; top: 92px; gap: 12px; }
  .card--front .brand__mark { width: 64px; height: 64px; }
  .card--front .brand__name { font-size: 40px; }

  .faint-ring {
    position: absolute;
    border-radius: 50%;
    border: 2px solid var(--faint);
  }
  .card--back .faint-ring { width: 90px; height: 90px; right: 30px; top: 40px; }
  .card--front .faint-ring { width: 116px; height: 116px; right: 34px; top: 26px; }

  .person { position: absolute; right: 0; top: 158px; text-align: right; }
  .person__name {
    font-family: "Lato", sans-serif;
    font-weight: 900;
    font-size: 22px;
    color: var(--text-dark);
    padding-right: 24px;
    letter-spacing: 0.2px;
  }
  .person__role {
    display: inline-block;
    margin-top: 4px;
    width: 170px;
    height: 22px;
    line-height: 22px;
    background: var(--brand-blue);
    color: #dce8f5;
    font-weight: 300;
    font-size: 14px;
    text-align: left;
    padding-left: 16px;
    border-radius: 11px 0 0 11px;
  }

  .contacts {
    position: absolute;
    left: 36px;
    top: 226px;
    display: grid;
    grid-template-columns: 218px auto;
    row-gap: 9px;
    font-family: "Josefin Sans", sans-serif;
    font-size: 15px;
    color: var(--text-dark);
  }
  .contacts__item { display: flex; align-items: center; gap: 9px; white-space: nowrap; }
  .contacts__icon { width: 15px; height: 15px; fill: var(--brand-blue); flex: none; }
</style>
</head>
<body>

  <section class="card card--back" aria-label="Card back">
    <svg class="card__bands" viewBox="0 0 560 320" aria-hidden="true">
      <path d="M0 0 H380 Q392 0 398 8 L402 14 H0 Z" fill="#0255a3"/>
      <path d="M560 294 V320 H160 Q170 306 186 306 H540 Q552 306 560 294 Z" fill="#0255a3"/>
    </svg>
    <div class="faint-ring" aria-hidden="true"></div>
    <div class="brand">
      <span class="brand__mark" aria-hidden="true"></span>
      <span class="brand__name">Lumenway</span>
    </div>
  </section>

  <section class="card card--front" aria-label="Card front">
    <svg class="card__bands" viewBox="0 0 560 320" aria-hidden="true">
      <path d="M150 0 H560 V12 H176 Q160 12 150 0 Z" fill="#0255a3"/>
      <path d="M0 306 H440 Q462 306 474 292 Q480 286 490 286 H560 V296 H498 Q488 296 482 304 Q470 320 446 320 H0 Z" fill="#0255a3"/>
    </svg>
    <div class="faint-ring" aria-hidden="true"></div>

    <div class="brand">
      <span class="brand__mark" aria-hidden="true"></span>
      <span class="brand__name">Lumenway</span>
    </div>

    <div class="person">
      <div class="person__name">YOUR NAME</div>
      <div class="person__role">Designation</div>
    </div>

    <div class="contacts">
      <div class="contacts__item">
        <svg class="contacts__icon" viewBox="0 0 16 16" aria-hidden="true"><path d="M8 1 L15 8 H13 V15 H9.5 V10.5 H6.5 V15 H3 V8 H1 Z"/></svg>
        Your Address Details Here
      </div>
      <div class="contacts__item">
        <svg class="contacts__icon" viewBox="0 0 16 16" aria-hidden="true"><path d="M4 1 H12 V5 H4 Z M1 6 H15 V12 H12.5 V10 H3.5 V12 H1 Z M4.5 11 H11.5 V15 H4.5 Z"/></svg>
        (555) 014-2217
      </div>
      <div class="contacts__item">
        <svg class="contacts__icon" viewBox="0 0 16 16" aria-hidden="true"><path d="M1 5 Q8 1 15 5 V7 H11.5 V5.5 H4.5 V7 H1 Z M3 8 H13 L14 15 H2 Z"/></svg>
        (555) 014-2210
      </div>
      <div class="contacts__item">
        <svg class="contacts__icon" viewBox="0 0 16 16" aria-hidden="true"><path d="M1 3 H15 V13 H1 Z M2.2 4 L8 9 L13.8 4 H12.6 L8 7.8 L3.4 4 Z"/></svg>
        info@lumenway.ca
      </div>
      <div class="contacts__item">
        <svg class="contacts__icon" viewBox="0 0 16 16" aria-hidden="true"><path d="M6.5 9.5 L9.5 6.5 M7 4.5 L9 2.5 A2.5 2.5 0 0 1 13.5 7 L11.5 9 M9 11.5 L7 13.5 A2.5 2.5 0 0 1 2.5 9 L4.5 7" fill="none" stroke="#0255a3" stroke-width="2" stroke-linecap="round"/></svg>
        www.lumenway.ca
      </div>
    </div>
  </section>

</body>
</html>
```